Business Card Design

It's an investment advisory service for individuals with all there investment needs. Also financial consulting to businesses and governmental agencies on retirement plans etc. It's personalized not commoditized help. Should show strength, knowledge and money orientation.

Reason: Will be out of town setting up office.

Reason: waiting for the 2/3rds of group to vote

Reason: only half the votes are in, I'm calling and getting verbals, but at this time we are down to 2 designs.

Industry/Entity Type

Investment

Contact Information for Business Card

B. Rel K. Financial Consulting and Wealth Management, Berislav Mike Holcek, 5172 Pasadena Loma Verde, San Diego, CA 94417-6381, Registered Investment Advisor

Requirements
Nice to have
• Something money oriented

```html
<!DOCTYPE html>
<html lang="en">
<head>
<meta charset="utf-8">
<title>B. Rel K. Business Card</title>
<link href="https://fonts.googleapis.com/css2?family=Open+Sans:wght@300;400;600;700&display=swap" rel="stylesheet">
<style>
  :root {
    --page-bg: #e9e7e3;
    --card-white: #fbfbfb;
    --brand-green: #12b46a;
    --brand-green-dark: #0c9a58;
    --text-grey: #9a9a9a;
    --text-white: #ffffff;
    --photo-tone-a: #e4ebe2;
    --photo-tone-b: #f6f7f4;
  }
  html, body {
    margin: 0;
    padding: 0;
    width: 1200px;
    height: 1000px;
    overflow: hidden;
    background: var(--page-bg);
    font-family: "Open Sans", Arial, sans-serif;
  }
  .card {
    position: absolute;
    left: 75px;
    top: 200px;
    width: 1050px;
    height: 600px;
    background: var(--card-white);
    box-shadow: 0 10px 30px rgba(0,0,0,0.15);
    overflow: hidden;
  }
  .brand-panel {
    position: absolute;
    left: 0;
    top: 0;
    width: 470px;
    height: 600px;
    background: var(--card-white);
  }
  .money-photo {
    position: absolute;
    right: 0;
    top: 0;
    width: 250px;
    height: 600px;
    background: linear-gradient(90deg, var(--photo-tone-b) 0%, var(--photo-tone-a) 60%, var(--photo-tone-b) 100%);
    opacity: 0.8;
  }
  .brand-mark {
    position: absolute;
    left: 90px;
    top: 190px;
    display: flex;
    align-items: center;
    gap: 18px;
  }
  .brand-square {
    width: 34px;
    height: 34px;
    border: 5px solid var(--brand-green);
    box-sizing: border-box;
  }
  .brand-name {
    font-weight: 700;
    font-size: 52px;
    color: var(--brand-green);
    letter-spacing: 1px;
  }
  .brand-tagline {
    position: absolute;
    left: 90px;
    top: 300px;
    font-weight: 400;
    font-size: 30px;
    line-height: 36px;
    color: var(--text-grey);
  }
  .contact-panel {
    position: absolute;
    left: 470px;
    top: 0;
    width: 580px;
    height: 600px;
    background: linear-gradient(135deg, var(--brand-green) 0%, var(--brand-green-dark) 100%);
  }
  .contact-icons {
    position: absolute;
    left: 40px;
    top: 190px;
    display: flex;
    gap: 8px;
  }
  .contact-block {
    position: absolute;
    left: 40px;
    top: 240px;
    color: var(--text-white);
  }
  .person-name {
    font-weight: 700;
    font-size: 34px;
    margin: 0;
    letter-spacing: 0.3px;
  }
  .credentials {
    font-weight: 600;
    font-size: 18px;
    margin: 2px 0 40px;
  }
  .phone {
    font-weight: 400;
    font-size: 26px;
    line-height: 36px;
    margin: 0;
    letter-spacing: 0.5px;
  }
</style>
</head>
<body>
  <div class="card">
    <section class="brand-panel">
      <div class="money-photo" role="img" aria-label="Faded photograph of stacked banknotes"></div>
      <div class="brand-mark">
        <span class="brand-square"></span>
        <span class="brand-name">B. Rel K.</span>
      </div>
      <div class="brand-tagline">Financial Consulting<br>and Wealth Management</div>
    </section>
    <section class="contact-panel">
      <div class="contact-icons">
        <svg width="36" height="36" viewBox="0 0 36 36" aria-hidden="true">
          <circle cx="18" cy="18" r="17" fill="#ffffff"/>
          <circle cx="18" cy="13" r="5.5" fill="#12b46a"/>
          <path d="M8 28c1-6 5-8 10-8s9 2 10 8z" fill="#12b46a"/>
        </svg>
        <svg width="36" height="36" viewBox="0 0 36 36" aria-hidden="true">
          <circle cx="18" cy="18" r="17" fill="#ffffff"/>
          <path d="M12 9l4 0 2 5-2.5 2c1 2.5 3 4.5 5.5 5.5l2-2.5 5 2 0 4c0 1-1 2-2 2-8 0-16-8-16-16 0-1 1-2 2-2z" fill="#12b46a"/>
        </svg>
      </div>
      <div class="contact-block">
        <h1 class="person-name">Berislav Mike Holcek</h1>
        <p class="credentials">MBA, RP®, CRC®</p>
        <p class="phone">619-555-0148</p>
        <p class="phone">775-555-0192</p>
      </div>
    </section>
  </div>
</body>
</html>
```